hotel's Website

Hotels website redesign for reference pictures, logo etc see http://restwellharbour.co.uk/

1. 2-3 Special offers on the main page.
2. Booking calender
3. Location Map
4. Picture gallery.
5. Journeymarks reviews.
6. short description
7. Social Media sharing.
8 Phone number and address.

Industry/Entity Type

Hotel

Requirements
Must have
• 1. 2-3 Special offers on the main page.
2. Booking calender
3. Location Map
4. Picture gallery.
5. Journeymarks reviews.
6. short description
7. Social Media sharing.

```html
<!DOCTYPE html>
<html lang="en">
<head>
<meta charset="utf-8">
<title>Restwell Harbour London – Victoria</title>
<link href="https://fonts.googleapis.com/css2?family=Noto+Serif:ital,wght@0,400;0,700;1,400&family=Open+Sans:wght@400;600;700&display=swap" rel="stylesheet">
<style>
:root{
  --page-dark:#1c1c1c;
  --bar-dark:#232323;
  --panel:#ffffff;
  --ink:#333333;
  --muted:#666666;
  --rule:#dddddd;
  --accent:#f0a21a;
  --link:#3fa9d6;
  --footer-text:#cfcfcf;
}
*{margin:0;padding:0;box-sizing:border-box}
html,body{width:1200px;height:1168px;overflow:hidden}
body{position:relative;background:var(--page-dark);font-family:"Open Sans",Arial,sans-serif;color:var(--ink)}
.abs{position:absolute}
h2,h3{font-weight:400}
.backdrop{left:0;top:0;width:1200px;height:1168px;background:radial-gradient(ellipse at 15% 25%,#4a4a4a 0%,#262626 40%,#161616 75%),#1a1a1a}
.backdrop-right{left:966px;top:0;width:234px;height:1168px;background:linear-gradient(180deg,#2b2b2b 0%,#3a3a3a 30%,#1e1e1e 70%,#2a2a2a 100%)}

/* top bar */
.topbar{left:0;top:0;width:1200px;height:24px;background:var(--bar-dark)}
.topbar-item{top:6px;font-size:8.5px;color:#e6e6e6;display:flex;align-items:center;gap:5px;white-space:nowrap}
.book-now{left:848px;top:4px;width:55px;height:15px;background:var(--accent);color:#fff;font-size:8.5px;font-weight:600;text-align:center;line-height:15px}

/* panel */
.panel{left:234px;top:24px;width:732px;height:861px;background:var(--panel)}
.pin-badge{left:316px;top:1px;width:34px;height:34px;border-radius:50%;background:var(--bar-dark);display:flex;align-items:center;justify-content:center}
.brand{left:300px;top:48px;display:flex;align-items:center;gap:6px}
.brand-mark{width:14px;height:14px;background:var(--accent)}
.brand-name{font-family:"Noto Serif",Georgia,serif;font-size:13px;color:#1f4ea3;line-height:1.15;width:76px}
.brand-tag{left:298px;top:103px;font-size:4.5px;letter-spacing:1.6px;color:#555;white-space:nowrap}
.nav-item{top:57px;font-family:"Noto Serif",Georgia,serif;font-size:8.5px;letter-spacing:.2px;color:#333;white-space:nowrap}
.nav-divider{top:54px;width:1px;height:22px;background:#ddd}
.nav-active{left:410px;top:112px;width:43px;height:3px;background:var(--accent)}

/* hero */
.hero{left:234px;top:116px;width:732px;height:328px;background:linear-gradient(90deg,#b08a55 0%,#d8c6a4 30%,#ece5d9 55%,#d9b57a 80%,#b77a3d 100%)}
.hero-floor{left:234px;top:300px;width:732px;height:144px;background:linear-gradient(180deg,rgba(190,40,30,.0) 0%,rgba(178,36,28,.75) 55%,#a8261e 100%)}
.caption-main{right:359px;top:207px;height:28px;padding:0 11px;background:var(--accent);color:#fff;font-family:"Noto Serif",Georgia,serif;font-style:italic;font-size:13px;line-height:28px;white-space:nowrap}
.caption-sub{left:493px;top:240px;width:383px;height:28px;background:rgba(40,40,40,.88);color:#fff;font-family:"Noto Serif",Georgia,serif;font-style:italic;font-size:13.5px;line-height:28px;text-align:center;white-space:nowrap}
.slide-arrow{top:256px;width:38px;height:38px;border-radius:50%;background:rgba(255,255,255,.8);display:flex;align-items:center;justify-content:center}

/* booking */
.booking{left:297px;top:407px;width:606px;height:66px;background:var(--bar-dark);border-bottom:3px solid var(--accent)}
.field{top:426px;height:22px;background:#fff;font-size:8px;color:#aaa;padding-left:6px;line-height:22px}
.field svg{position:absolute;right:8px;top:7px}
.check-btn{left:795px;top:426px;width:81px;height:20px;background:var(--accent);color:#fff;font-size:8px;font-weight:600;text-align:center;line-height:20px;white-space:nowrap}

/* sections */
.section-title{font-family:"Noto Serif",Georgia,serif;font-style:italic;font-weight:400;font-size:11px;color:#333;white-space:nowrap}
.section-rule{height:1px;background:var(--rule)}
.section-accent{height:3px;width:40px;background:var(--accent)}
.photo{display:block}
.body-text{font-size:8px;line-height:12.5px;color:#333}
.more-btn{border:1px solid #ccc;font-size:8.5px;color:#444;text-align:center;background:#fff}
.offer-title{font-size:8.5px;color:#333;white-space:nowrap}
.offer-more{width:39px;height:12px;border:1px solid #ccc;font-size:5.5px;line-height:10px;text-align:center;color:#555}
.gallery-nav{top:751px;width:16px;height:16px;border:1px solid #999;border-radius:50%;display:flex;align-items:center;justify-content:center}

/* footer */
.foot-title{top:919px;font-size:7.5px;font-weight:700;letter-spacing:.6px;color:#fff;white-space:nowrap}
.foot-accent{top:938px;width:42px;height:3px;background:var(--accent)}
.foot-text{font-size:7.5px;line-height:11.5px;color:var(--footer-text)}
.foot-links{left:297px;top:1009px;font-size:7.5px;line-height:12px;color:var(--link);white-space:nowrap}
.foot-btn{height:21px;background:var(--accent);color:#fff;font-size:8.5px;text-align:center;line-height:21px}
.email-input{left:452px;top:997px;width:129px;height:24px;background:#fff;font-size:8px;color:#aaa;padding-left:8px;line-height:24px}
.review-widget{left:607px;top:959px;width:119px;height:132px;background:#fff;padding:4px}
.review-head{font-size:9px;font-weight:600;color:#333;text-align:center;height:18px;line-height:18px}
.review-search{height:13px;background:#5c8f4e;padding:2px 3px}
.review-search div{height:9px;background:#fff;font-size:4.5px;color:#999;line-height:9px;padding-left:3px}
.review-group{background:#d6e6cf;font-size:5.5px;font-weight:700;color:#333;padding:3px 3px 2px}
.review-row{height:16px;border:1px solid #ddd;background:#fff;font-size:5.5px;font-weight:600;color:#333;line-height:14px;padding-left:6px;margin:2px 3px 0;position:relative}
.review-row::after{content:"›";position:absolute;right:5px;top:0;font-size:8px;color:#777}
.social{top:951px;width:24px;height:24px;border-radius:50%;background:#fff}
.copyright-rule{left:297px;top:1122px;width:606px;height:1px;background:#444}
.copyright{left:297px;top:1140px;font-size:7.5px;color:var(--footer-text);white-space:nowrap}
</style>
</head>
<body>
<div class="abs backdrop" role="img" aria-label="Night view of London landmarks in black and white"></div>
<div class="abs backdrop-right" role="img" aria-label="Night view of the river and observation wheel"></div>

<header>
  <div class="abs topbar"></div>
  <div class="abs topbar-item" style="left:540px">
    <svg width="8" height="8" viewBox="0 0 10 10"><path d="M2 1l2 2-1 1.5c.6 1.2 1.4 2 2.5 2.5L7 6l2 2-1.5 1.5C4.5 9 1 5.5.5 2.5z" fill="#e6e6e6"/></svg>+ 44 (0) 20 7946 0123
  </div>
  <div class="abs topbar-item" style="left:648px">
    <svg width="9" height="7" viewBox="0 0 9 7"><rect width="9" height="7" fill="#e6e6e6"/><path d="M0 0l4.5 4L9 0" stroke="#232323" fill="none"/></svg>stay@restwellharbour.co.uk
  </div>
  <div class="abs topbar-item" style="left:795px">English
    <svg width="6" height="4" viewBox="0 0 6 4"><path d="M0 0h6L3 4z" fill="#e6e6e6"/></svg>
  </div>
  <div class="abs book-now">Book Now</div>
</header>

<main>
  <div class="abs panel"></div>
  <div class="abs pin-badge">
    <svg width="11" height="14" viewBox="0 0 11 14"><path d="M5.5 0A5.5 5.5 0 0 0 0 5.5C0 9 5.5 14 5.5 14S11 9 11 5.5A5.5 5.5 0 0 0 5.5 0z" fill="#fff"/><circle cx="5.5" cy="5.3" r="2" fill="#232323"/></svg>
  </div>
  <div class="abs brand"><div class="brand-mark"></div><div class="brand-name">Restwell Harbour</div></div>
  <div class="abs brand-tag">BY HARBOURLINE HOTELS</div>

  <nav>
    <span class="abs nav-item" style="left:412px">HOME</span>
    <span class="abs nav-divider" style="left:446px"></span>
    <span class="abs nav-item" style="left:456px">OUR ROOMS</span>
    <span class="abs nav-divider" style="left:518px"></span>
    <span class="abs nav-item" style="left:528px">ATTRACTIONS</span>
    <span class="abs nav-divider" style="left:597px"></span>
    <span class="abs nav-item" style="left:608px">LONDON EVENTS</span>
    <span class="abs nav-divider" style="left:689px"></span>
    <span class="abs nav-item" style="left:700px">SPECIAL OFFERS</span>
    <span class="abs nav-divider" style="left:782px"></span>
    <span class="abs nav-item" style="left:793px">PHOTOS</span>
    <span class="abs nav-divider" style="left:837px"></span>
    <span class="abs nav-item" style="left:848px">DIRECTIONS</span>
    <span class="abs nav-divider" style="left:910px"></span>
    <span class="abs nav-item" style="left:921px">CONTACT</span>
  </nav>
  <div class="abs nav-active"></div>

  <section>
    <div class="abs hero" role="img" aria-label="Hotel bedroom with a double bed, red cushions and wooden furniture"></div>
    <div class="abs hero-floor"></div>
    <div class="abs caption-main">Enjoy your stay at Restwell Harbour London – Victoria</div>
    <div class="abs caption-sub">Be sure that you’ve found our best value on the Internet.</div>
    <div class="abs slide-arrow" style="left:262px"><svg width="8" height="14" viewBox="0 0 8 14"><path d="M7 1L1 7l6 6" stroke="#555" fill="none" stroke-width="1.2"/></svg></div>
    <div class="abs slide-arrow" style="left:899px"><svg width="8" height="14" viewBox="0 0 8 14"><path d="M1 1l6 6-6 6" stroke="#555" fill="none" stroke-width="1.2"/></svg></div>
  </section>

  <form class="abs booking" aria-label="Booking"></form>
  <div class="abs field" style="left:316px;width:118px">Check In<svg width="9" height="9" viewBox="0 0 9 9"><rect x=".5" y="1.5" width="8" height="7" fill="none" stroke="#666"/><path d="M.5 3.5h8M3 5h1M5 5h1M3 7h1M5 7h1" stroke="#666"/></svg></div>
  <div class="abs field" style="left:441px;width:118px">Check Out<svg width="9" height="9" viewBox="0 0 9 9"><rect x=".5" y="1.5" width="8" height="7" fill="none" stroke="#666"/><path d="M.5 3.5h8M3 5h1M5 5h1M3 7h1M5 7h1" stroke="#666"/></svg></div>
  <div class="abs field" style="left:566px;width:107px">Adults<svg width="8" height="5" viewBox="0 0 8 5" style="top:9px"><path d="M0 0h8L4 5z" fill="#333"/></svg></div>
  <div class="abs field" style="left:680px;width:107px">Children<svg width="8" height="5" viewBox="0 0 8 5" style="top:9px"><path d="M0 0h8L4 5z" fill="#333"/></svg></div>
  <div class="abs check-btn">Check Availability</div>

  <section>
    <h2 class="abs section-title" style="left:297px;top:493px">About Restwell Harbour</h2>
    <div class="abs section-rule" style="left:297px;top:515px;width:189px"></div>
    <div class="abs section-accent" style="left:297px;top:515px"></div>
    <div class="abs photo" style="left:297px;top:535px;width:189px;height:101px;background:linear-gradient(180deg,#c9b08a 0%,#e8e2d8 45%,#f2f2f0 70%,#6b5b4b 100%)" role="img" aria-label="White Georgian townhouse hotel front with railings"></div>
    <p class="abs body-text" style="left:297px;top:651px;width:192px">This tastefully appointed four storey building is comprised of three attractive Georgian style townhouses...</p>
    <div class="abs more-btn" style="left:297px;top:702px;width:58px;height:21px;line-height:19px">Read More</div>
  </section>

  <section>
    <h2 class="abs section-title" style="left:505px;top:493px">Special Offers</h2>
    <div class="abs section-rule" style="left:505px;top:515px;width:189px"></div>
    <div class="abs section-accent" style="left:505px;top:515px"></div>

    <div class="abs photo" style="left:504px;top:536px;width:45px;height:38px;background:linear-gradient(135deg,#e9d2bd,#c9a07c)" role="img" aria-label="Spa treatment"></div>
    <div class="abs offer-title" style="left:560px;top:539px">25% off on Spa Treatments</div>
    <div class="abs offer-more" style="left:560px;top:557px">Read More</div>

    <div class="abs photo" style="left:504px;top:582px;width:45px;height:39px;background:linear-gradient(135deg,#f2f2f2,#bdbdbd)" role="img" aria-label="Calendar page"></div>
    <div class="abs offer-title" style="left:560px;top:585px">Sunday Special</div>
    <div class="abs offer-more" style="left:560px;top:603px">Read More</div>

    <div class="abs photo" style="left:504px;top:628px;width:45px;height:39px;background:linear-gradient(135deg,#8ea0b8,#6b5a4e)" role="img" aria-label="Shoppers on a London street"></div>
    <div class="abs offer-title" style="left:560px;top:631px">Shopping in London</div>
    <div class="abs offer-more" style="left:560px;top:650px">Read More</div>

    <div class="abs photo" style="left:504px;top:676px;width:45px;height:39px;background:linear-gradient(180deg,#d9e3d0,#3a3a3a)" role="img" aria-label="Hire car"></div>
    <div class="abs offer-title" style="left:560px;top:679px">Low Cost Car Hire</div>
    <div class="abs offer-more" style="left:560px;top:697px">Read More</div>
  </section>

  <section>
    <h2 class="abs section-title" style="left:713px;top:493px">London Events</h2>
    <div class="abs section-rule" style="left:713px;top:515px;width:189px"></div>
    <div class="abs section-accent" style="left:713px;top:515px"></div>
    <div class="abs photo" style="left:713px;top:535px;width:190px;height:101px;background:linear-gradient(180deg,#3b3128 0%,#5a3a22 55%,#c4621c 85%,#8a3a14 100%)" role="img" aria-label="Halloween display with pumpkins"></div>
    <p class="abs body-text" style="left:713px;top:651px;width:190px">Halloween at the Thameside Vaults<br>(26th Oct 13 to 3rd Nov 13)</p>
    <div class="abs more-btn" style="left:713px;top:690px;width:58px;height:21px;line-height:19px">Read More</div>
  </section>

  <section>
    <h2 class="abs section-title" style="left:297px;top:750px">Picture Gallery</h2>
    <div class="abs section-rule" style="left:297px;top:775px;width:606px"></div>
    <div class="abs gallery-nav" style="left:864px"><svg width="5" height="8" viewBox="0 0 5 8"><path d="M4 1L1 4l3 3" stroke="#333" fill="none"/></svg></div>
    <div class="abs gallery-nav" style="left:885px"><svg width="5" height="8" viewBox="0 0 5 8"><path d="M1 1l3 3-3 3" stroke="#333" fill="none"/></svg></div>

    <div class="abs photo" style="left:297px;top:796px;width:76px;height:57px;background:linear-gradient(135deg,#8a8170,#d9c23a 60%,#3a3a3a)" role="img" aria-label="Reception desk"></div>
    <div class="abs photo" style="left:385px;top:796px;width:76px;height:57px;background:linear-gradient(180deg,#e6dccb,#b8392d)" role="img" aria-label="Twin bedroom"></div>
    <div class="abs photo" style="left:473px;top:796px;width:77px;height:57px;background:linear-gradient(135deg,#4e4a48,#e0a72a 55%,#d8443a)" role="img" aria-label="Lounge with colourful seating"></div>
    <div class="abs photo" style="left:562px;top:796px;width:76px;height:57px;background:linear-gradient(135deg,#d8d0c0,#8a6a45)" role="img" aria-label="Dining corner"></div>
    <div class="abs photo" style="left:650px;top:796px;width:76px;height:57px;background:linear-gradient(180deg,#e9d9a0,#a8261e)" role="img" aria-label="Room with red carpet"></div>
    <div class="abs photo" style="left:738px;top:796px;width:77px;height:57px;background:linear-gradient(135deg,#d6c6b0,#9a5a36)" role="img" aria-label="Breakfast room"></div>
    <div class="abs photo" style="left:827px;top:796px;width:76px;height:57px;background:linear-gradient(135deg,#d8d4cc,#e8d43a 55%,#c8364a)" role="img" aria-label="Sofa with cushions"></div>
  </section>
</main>

<footer>
  <h3 class="abs foot-title" style="left:297px">PARTNER’S HOTEL</h3>
  <div class="abs foot-accent" style="left:297px"></div>
  <p class="abs foot-text" style="left:297px;top:956px;width:140px">This hotel is owned and operated by the Fourpoint Hotel Group, please take a look of some of our other hotels below:</p>
  <div class="abs foot-links">Larkspur House - Camden Row<br>Larkspur Express - Earls Row<br>Meridian Court Hotel<br>Budgetbay Victoria</div>
  <div class="abs foot-btn" style="left:297px;top:1067px;width:58px">Read More</div>

  <h3 class="abs foot-title" style="left:452px">NEWSLETTER</h3>
  <div class="abs foot-accent" style="left:452px"></div>
  <p class="abs foot-text" style="left:452px;top:956px;width:135px;color:#fff;font-weight:600">Sign up for our newsletter for latest news</p>
  <div class="abs email-input">Email</div>
  <div class="abs foot-btn" style="left:452px;top:1033px;width:58px">Subscribe</div>

  <h3 class="abs foot-title" style="left:606px">JOURNEYMARKS</h3>
  <div class="abs foot-accent" style="left:606px"></div>
  <div class="abs review-widget">
    <div class="review-head">Journeymarks</div>
    <div class="review-search"><div>Search Journeymarks</div></div>
    <div class="review-group">Find Places</div>
    <div class="review-row">Hotels</div>
    <div class="review-row">Restaurants</div>
    <div class="review-row">Things to do</div>
    <div class="review-row" style="margin-top:5px">Write a Review</div>
  </div>

  <h3 class="abs foot-title" style="left:761px">SOCIAL MEDIA</h3>
  <div class="abs foot-accent" style="left:761px"></div>
  <div class="abs social" style="left:761px" role="img" aria-label="Social network link"></div>
  <div class="abs social" style="left:789px" role="img" aria-label="Social network link"></div>
  <div class="abs social" style="left:817px" role="img" aria-label="Social network link"></div>
  <div class="abs social" style="left:846px" role="img" aria-label="Social network link"></div>
  <div class="abs social" style="left:874px" role="img" aria-label="Social network link"></div>

  <div class="abs copyright-rule"></div>
  <p class="abs copyright">© Copyright 2013. Restwell Harbour Victoria. All Rights Reserved</p>
</footer>
</body>
</html>
```